Custom Manufacturing Company square space website design

I own a custom manufacturing company that uses precision cutting technology to manufacture project components over a couple industries. We have an industrial CNC router and state of the art edge bander and cut a lot of cabinetry components for cabinet shops, builders, closet companies, ect. We offer design and assembly for any cabinetry or can build cabinets to spec. We also cut components for other industries out of wood, plastics, acryclics, ect. We offer design engineering services, product development protype services. we have a 3D printer farm. We want our communicate trust, dependability, and the value we place on client relationships.

We essentially want a credibility website. Landing page and drops downs for services we offer, capabilites, about us, contact

```html
<!DOCTYPE html>
<html lang="en">
<head>
<meta charset="utf-8">
<title>North Lake CNC</title>
<link href="https://fonts.googleapis.com/css2?family=Montserrat:wght@400;500;600;700;800&display=swap" rel="stylesheet">
<style>
:root{
  --ink:#0b0b0b;
  --white:#ffffff;
  --text:#333333;
  --muted:#555555;
  --line:#d8d8d8;
  --dark:#151413;
  --hero-a:#5a5a5c;
  --hero-b:#2c2c2e;
}
*{box-sizing:border-box;margin:0;padding:0}
html,body{width:1200px;height:4113px;overflow:hidden}
body{position:relative;font-family:"Montserrat",sans-serif;color:var(--text);background:var(--white)}
.abs{position:absolute}
/* header */
.topbar{left:420px;top:0;width:780px;height:57px;background:var(--ink);clip-path:polygon(0 0,100% 0,100% 100%,36px 100%)}
.topbar .item{position:absolute;top:0;height:57px;display:flex;align-items:center;gap:10px;color:var(--white);font-size:14px;font-weight:700;line-height:1.3}
.ico{width:22px;height:22px;flex:none}
.brand{left:110px;top:12px;width:215px;display:flex;flex-direction:column;align-items:center}
.brand .mark{width:84px;height:62px;border:3px solid var(--ink)}
.brand .name{margin-top:10px;font-size:22px;font-weight:600;letter-spacing:4px;color:var(--ink);white-space:nowrap}
.nav{left:484px;top:84px;display:flex;gap:52px;align-items:center;font-size:16px;font-weight:600;color:var(--ink)}
.nav .active{text-decoration:underline;text-underline-offset:5px}
.nav .dd::after{content:"";display:inline-block;margin-left:6px;border:6px solid transparent;border-top:8px solid var(--ink);border-bottom:0;vertical-align:middle}
.btn-dark{background:var(--ink);color:var(--white);font-weight:700;display:flex;align-items:center;justify-content:center}
.contact-btn{left:1012px;top:76px;width:112px;height:38px;font-size:15px}
/* hero */
.hero{left:0;top:145px;width:1200px;height:549px;background:linear-gradient(100deg,#6d6d6f 0%,var(--hero-a) 35%,var(--hero-b) 70%,#4a4a4c 100%)}
.hero h1{position:absolute;left:110px;top:188px;color:var(--white);font-weight:500;font-size:32px;line-height:1}
.hero h1 strong{display:block;font-size:50px;font-weight:800;margin-top:16px}
.hero .cta{left:110px;top:300px;width:139px;height:34px;background:var(--white);color:var(--ink);font-size:15px;font-weight:700}
.dots{left:1140px;top:182px;display:flex;flex-direction:column;gap:16px}
.dots span{width:5px;height:26px;background:var(--white)}
/* about */
.section-title{font-weight:700;color:var(--ink);font-size:32px}
.about-title{left:108px;top:774px}
.about-text{left:110px;top:834px;width:447px;font-size:13.5px;line-height:30.7px;text-align:justify;color:#222}
.read-more{left:108px;top:1090px;width:133px;height:36px;font-size:15px}
.about-shadow{left:660px;top:820px;width:418px;height:314px;border:5px solid var(--ink);border-left:none;border-top:none}
.about-photo{left:645px;top:806px;width:420px;height:314px;background:linear-gradient(120deg,#9a7a56,#c9a77a 55,#6f6a66);background:linear-gradient(120deg,#8b6d4d 0%,#c4a27a 55%,#5e5b59 100%)}
/* carousels */
.band{left:0;width:1200px;background:radial-gradient(ellipse at 60% 40%,#3a3836 0%,var(--dark) 75%)}
.cap-band{top:1216px;height:501px}
.band-title{position:absolute;left:0;width:1200px;text-align:center;color:var(--white);font-size:32px;font-weight:700}
.card{position:absolute;width:308px;height:348px;background:var(--white);box-shadow:0 2px 8px rgba(0,0,0,.18)}
.card .ph{position:absolute;left:11px;top:13px;width:286px;height:283px}
.card .lbl{position:absolute;left:0;bottom:18px;width:100%;text-align:center;font-weight:700;font-size:16px;color:var(--ink)}
.arrow{position:absolute;width:18px;height:24px}
.underline{position:absolute;height:4px;background:var(--ink)}
/* contact */
.contact-band{top:2330px;height:540px}
.field{position:absolute;background:var(--white);border-radius:6px;display:flex;align-items:center;gap:10px;padding-left:14px;font-size:12.5px;color:#777}
.field svg{width:14px;height:14px;flex:none}
.submit{left:535px;top:2779px;width:131px;height:38px;background:var(--white);color:var(--ink);font-weight:700;font-size:15px}
/* values */
.value{position:absolute;top:3058px;width:330px;text-align:center}
.value .circle{width:90px;height:90px;border-radius:50%;background:var(--ink);margin:0 auto;display:flex;align-items:center;justify-content:center}
.value h3{margin-top:36px;font-size:19px;font-weight:700;color:var(--ink)}
.value p{margin-top:14px;font-size:13px;line-height:25.8px;color:var(--muted)}
.divider{position:absolute;top:3072px;width:2px;height:303px;background:var(--ink)}
/* newsletter + footer */
.footer{left:0;top:3628px;width:1200px;height:485px;background:var(--ink)}
.news{left:110px;top:3473px;width:977px;height:252px;background:var(--white);box-shadow:0 3px 10px rgba(0,0,0,.15)}
.news h2{position:absolute;top:48px;width:100%;text-align:center;font-size:29px;font-weight:700;color:var(--ink)}
.news .input{position:absolute;left:54px;top:112px;width:730px;height:75px;border:1px solid #333;display:flex;align-items:center;padding-left:38px;font-size:15px;color:#222}
.news .sub{position:absolute;left:784px;top:112px;width:139px;height:75px;font-size:15px}
.f-brand{left:110px;top:3812px;width:260px;display:flex;flex-direction:column;align-items:center}
.f-brand .mark{width:106px;height:76px;border:3px solid var(--white)}
.f-brand .name{margin-top:14px;font-size:27px;font-weight:600;letter-spacing:5px;color:var(--white);white-space:nowrap}
.social{left:182px;top:3980px;display:flex;gap:8px}
.social span{width:22px;height:22px;background:var(--white)}
.fcol{position:absolute;top:3810px;color:var(--white)}
.fcol h4{font-size:16px;font-weight:700;margin-bottom:14px}
.fcol a{display:block;color:var(--white);text-decoration:none;font-size:15.5px;line-height:37px}
.fcontact{left:884px}
.fcontact .row{display:flex;gap:14px;font-size:15.5px;line-height:1.4;margin-bottom:22px}
.frule{left:110px;top:4046px;width:980px;height:1px;background:#777}
.copy{left:0;top:4070px;width:1200px;text-align:center;color:var(--white);font-size:15px}
</style>
</head>
<body>

<!-- header -->
<div class="abs topbar">
  <div class="item" style="left:58px">
    <svg class="ico" viewBox="0 0 24 24"><rect x="1" y="1" width="22" height="22" rx="4" fill="#fff"/><path d="M12 5a5 5 0 0 0-5 5c0 4 5 9 5 9s5-5 5-9a5 5 0 0 0-5-5zm0 7a2 2 0 1 1 0-4 2 2 0 0 1 0 4z" fill="#000"/></svg>
    <span>220 Harbor Ave NE<br>Lakeview, MN 55100</span>
  </div>
  <div class="item" style="left:314px">
    <svg class="ico" viewBox="0 0 24 24"><rect x="1" y="1" width="22" height="22" rx="4" fill="#fff"/><path d="M8 5l3 3-2 2c1 2 3 4 5 5l2-2 3 3-2 3C10 19 5 14 5 7z" fill="#000"/></svg>
    <span>(555) 014-2290</span>
  </div>
  <div class="item" style="left:518px">
    <svg class="ico" viewBox="0 0 24 24"><rect x="1" y="1" width="22" height="22" rx="4" fill="#fff"/><path d="M5 7h14v10H5z" fill="none" stroke="#000" stroke-width="1.8"/><path d="M5 7l7 6 7-6" fill="none" stroke="#000" stroke-width="1.8"/></svg>
    <span>info@northlakecnc.com</span>
  </div>
</div>

<div class="abs brand">
  <div class="mark"></div>
  <div class="name">NORTH LAKE CNC</div>
</div>

<nav class="abs nav">
  <span class="active">Home</span>
  <span class="dd">Industries</span>
  <span class="dd">Capabilities</span>
  <span class="dd">About Us</span>
</nav>
<div class="abs btn-dark contact-btn">CONTACT</div>

<!-- hero -->
<section class="abs hero" role="img" aria-label="Modern dark grey kitchen with wall cabinets and breakfast counter">
  <h1>WELCOME TO<strong>NORTH LAKE CNC</strong></h1>
  <div class="abs cta" style="display:flex;align-items:center;justify-content:center">GET STARTED</div>
  <div class="abs dots" style="top:182px"><span></span><span></span><span></span></div>
</section>

<!-- about -->
<h2 class="abs section-title about-title">ABOUT US</h2>
<p class="abs about-text">Lorem ipsum dolor sit amet, consectetur adipiscing elit, sed do eiusmod tempor incididunt ut labore et dolore magna aliqua. Ut enim ad minim veniam, quis nostrud exercitation ullamco laboris nisi ut aliquip ex ea commodo consequat. Duis aute irure dolor in reprehenderit in voluptate velit esse cillum dolore eu fugiat nulla pariatur. Excepteur sint occaecat cupidatat non proident, sunt in culpa qui officia deserunt mollit anim id est laborum</p>
<div class="abs btn-dark read-more">READ MORE</div>
<div class="abs about-shadow"></div>
<div class="abs about-photo" role="img" aria-label="Craftsman assembling a wooden shelving unit"></div>

<!-- capabilities -->
<section class="abs band cap-band">
  <h2 class="band-title" style="top:40px">CAPABILITIES</h2>
  <svg class="arrow" style="left:46px;top:264px" viewBox="0 0 18 24"><path d="M13 3L5 12l8 9" fill="none" stroke="#fff" stroke-width="4"/></svg>
  <svg class="arrow" style="left:1126px;top:264px" viewBox="0 0 18 24"><path d="M5 3l8 9-8 9" fill="none" stroke="#fff" stroke-width="4"/></svg>
  <div class="card" style="left:113px;top:91px"><div class="ph" role="img" aria-label="CNC router cutting a wood panel" style="background:linear-gradient(135deg,#c45a2a,#b8875a 50%,#6b5a48)"></div><div class="lbl">CNC ROUTING</div></div>
  <div class="card" style="left:445px;top:91px"><div class="ph" role="img" aria-label="Worker feeding a panel through an edge bander" style="background:linear-gradient(160deg,#7f7566,#3a86c8 40%,#e0c04a 70%,#d2632b)"></div><div class="lbl">EDGE BANDING</div></div>
  <div class="card" style="left:777px;top:91px"><div class="ph" role="img" aria-label="3D rendered closet shelving layout" style="background:linear-gradient(180deg,#f1f1f1,#cfcfcf 60%,#e8e8e8)"></div><div class="lbl">3D PRINTING</div></div>
</section>

<!-- industries -->
<h2 class="abs section-title" style="left:0;top:1788px;width:1200px;text-align:center">INDUSTRIES</h2>
<div class="underline" style="left:548px;top:1837px;width:106px"></div>
<svg class="arrow" style="left:46px;top:2046px" viewBox="0 0 18 24"><path d="M13 3L5 12l8 9" fill="none" stroke="#000" stroke-width="4"/></svg>
<svg class="arrow" style="left:1126px;top:2046px" viewBox="0 0 18 24"><path d="M5 3l8 9-8 9" fill="none" stroke="#000" stroke-width="4"/></svg>
<div class="card" style="left:113px;top:1875px"><div class="ph" role="img" aria-label="Black kitchen cabinetry with open wood shelves" style="background:linear-gradient(135deg,#8a8a8a,#1e1e1e 45%,#5a4632)"></div><div class="lbl">CABINETRY</div></div>
<div class="card" style="left:445px;top:1875px"><div class="ph" role="img" aria-label="Walk-in closet with wooden shelving" style="background:linear-gradient(135deg,#b89a78,#4a3e34 55%,#9c8066)"></div><div class="lbl">CLOSET COMPANIES</div></div>
<div class="card" style="left:777px;top:1875px"><div class="ph" role="img" aria-label="Wooden staircase with built-in drawers" style="background:linear-gradient(135deg,#e6e1da,#c8a27a 55%,#a57c54)"></div><div class="lbl">CUSTOM MANUFACTURING</div></div>

<!-- contact -->
<section class="abs band contact-band">
  <h2 class="band-title" style="top:42px">CONTACT US</h2>
  <div class="underline" style="left:548px;top:95px;width:106px;background:#fff"></div>
</section>
<div class="field" style="left:144px;top:2469px;width:448px;height:43px"><svg viewBox="0 0 14 14"><circle cx="7" cy="4" r="3" fill="#222"/><path d="M1 14a6 5 0 0 1 12 0z" fill="#222"/></svg>Name</div>
<div class="field" style="left:613px;top:2469px;width:452px;height:43px"><svg viewBox="0 0 14 14"><rect x="1" y="3" width="12" height="8" fill="none" stroke="#222" stroke-width="1.6"/><path d="M1 3l6 5 6-5" fill="none" stroke="#222" stroke-width="1.6"/></svg>Email</div>
<div class="field" style="left:144px;top:2528px;width:448px;height:43px"><svg viewBox="0 0 14 14"><path d="M3 1l3 3-1.5 1.5c1 1.6 2.4 3 4 4L10 8l3 3-2 2C6 12 2 8 1 3z" fill="#222"/></svg>Contact Number</div>
<div class="field" style="left:613px;top:2528px;width:452px;height:43px"><svg viewBox="0 0 14 14"><rect x="2" y="1" width="10" height="12" fill="none" stroke="#222" stroke-width="1.6"/><path d="M4.5 5h5M4.5 8h5" stroke="#222" stroke-width="1.4"/></svg>Subject</div>
<div class="field" style="left:144px;top:2589px;width:921px;height:164px;align-items:flex-start;padding-top:14px"><svg viewBox="0 0 14 14"><ellipse cx="7" cy="6.5" rx="6" ry="5" fill="#222"/><path d="M3 10l-1 3 4-2z" fill="#222"/></svg>Your Messsage</div>
<div class="abs submit" style="display:flex;align-items:center;justify-content:center">SUBMIT</div>

<!-- values -->
<h2 class="abs section-title" style="left:0;top:2948px;width:1200px;text-align:center">VALUES</h2>
<div class="underline" style="left:546px;top:2996px;width:106px"></div>
<div class="value" style="left:95px">
  <div class="circle"><svg width="44" height="44" viewBox="0 0 44 44"><path d="M8 24l8-8h12l8 8-10 8H18z" fill="none" stroke="#fff" stroke-width="3"/></svg></div>
  <h3>COMMUNICATE TRUST</h3>
  <p>Communication At the heart of any good relationship is communication. We make sure we are available to our clients and understand the importance of affective communication to problem solve and move the ball forward with every project.</p>
</div>
<div class="divider" style="left:437px"></div>
<div class="value" style="left:449px">
  <div class="circle"><svg width="44" height="44" viewBox="0 0 44 44"><path d="M12 16h20l-10 14z" fill="none" stroke="#fff" stroke-width="3"/><path d="M10 36h24" stroke="#fff" stroke-width="3"/></svg></div>
  <h3>DEPENDABILITY</h3>
  <p>Dependability Trust is built through time and action. Our team is dedicated to ensuring that promises made are promises kept. From the precision in our manufacturing process to the punctualities of our deliveries, dependability is woven into every aspect of our work</p>
</div>
<div class="divider" style="left:809px"></div>
<div class="value" style="left:805px">
  <div class="circle"><svg width="44" height="44" viewBox="0 0 44 44"><circle cx="22" cy="20" r="11" fill="none" stroke="#fff" stroke-width="3"/><path d="M16 36h12" stroke="#fff" stroke-width="3"/></svg></div>
  <h3>THE VALUE</h3>
  <p>Creating Value Creating value is not only a goal at North Lake CNC, it's our guiding principle. We believe true success lies not only in the products we manufacture but in the lasting value we provide our clients.</p>
</div>

<!-- footer -->
<footer class="abs footer"></footer>
<div class="abs news">
  <h2>NEWSLETTER SIGNUP</h2>
  <div class="input">Enter Your Email Address</div>
  <div class="sub btn-dark">SUBSCRIBE</div>
</div>

<div class="abs f-brand">
  <div class="mark"></div>
  <div class="name">NORTH LAKE CNC</div>
</div>
<div class="abs social" aria-label="Social links"><span></span><span></span><span></span><span></span></div>

<div class="fcol" style="left:460px">
  <h4>QUICK LINKS</h4>
  <a>Home</a><a>Industries</a><a>Capabilities</a><a>About Us</a><a>Contact</a>
</div>
<div class="fcol" style="left:662px">
  <h4>HELP LINKS</h4>
  <a>Privacy Policy</a><a>Terms &amp; Conditions</a>
</div>
<div class="fcol fcontact">
  <h4>CONTACT DETAIL</h4>
  <div class="row"><svg class="ico" viewBox="0 0 24 24"><rect x="1" y="1" width="22" height="22" rx="4" fill="#fff"/><path d="M12 5a5 5 0 0 0-5 5c0 4 5 9 5 9s5-5 5-9a5 5 0 0 0-5-5zm0 7a2 2 0 1 1 0-4 2 2 0 0 1 0 4z" fill="#000"/></svg><span>220 Harbor Ave NE,<br>Lakeview, MN 55100</span></div>
  <div class="row"><svg class="ico" viewBox="0 0 24 24"><rect x="1" y="1" width="22" height="22" rx="4" fill="#fff"/><path d="M8 5l3 3-2 2c1 2 3 4 5 5l2-2 3 3-2 3C10 19 5 14 5 7z" fill="#000"/></svg><span>(555) 014-2290</span></div>
  <div class="row"><svg class="ico" viewBox="0 0 24 24"><rect x="1" y="1" width="22" height="22" rx="4" fill="#fff"/><path d="M5 7h14v10H5z" fill="none" stroke="#000" stroke-width="1.8"/><path d="M5 7l7 6 7-6" fill="none" stroke="#000" stroke-width="1.8"/></svg><span>info@northlakecnc.com</span></div>
</div>
<div class="abs frule"></div>
<div class="abs copy">© 2023 North Lake CNC. All rights reserved.</div>

</body>
</html>
```